Innovation Company Business Card Design

I need to have my business card updated. The current card was designed when the company started 2.5 years ago and was a quick and dirty job.

I need a new card design that is more professional and has my updated company tag line.

I will include the old card's Corel Draw file, and EPS versions as examples of the current design. I will also include the company logo eps and corel version files.

The company pantone colour is pantone 1805 c (a dark red)

I want the design to convey the nature of our business as a strategic technology innovation company, but yet still be professional. We are funky vibey and work from an industrial style office in a vibey designer dominat part of town. Though are clients include large banks and corporate clients too.

The information that needs to be on the card is in attached word document (but doesn't have to be in this order or format)

Final version needs to be supplied in PNG preview, as well as PSD file format (or other editable file version) so that personal information on card can be easily edited and reprinted.

Target Market(s)

CEO's of small to medium size companies
Marketing Managers of large coporates
Account managers of Digital Agencies

Industry/Entity Type

Business

Requirements
Must have
• 86x54mm will be cut in rounded corner credit card size format (Except if you recommend otherwise in your design)
Nice to have
• Some kind of background transparency combined with the pantone colour that gives the card some dimension and depth. But no gradient fills please :-)
Should not have
• Basic gradient fills
• Clipart

```html
<!DOCTYPE html>
<html lang="en">
<head>
<meta charset="utf-8">
<title>Brightvale Business Card</title>
<link rel="stylesheet" href="https://fonts.googleapis.com/css2?family=Open+Sans:wght@400;600;700;800&family=Arimo:wght@400&display=swap">
<style>
  :root {
    --brand-red: #bd2e1c;
    --paper: #ffffff;
    --ink: #4a4a4a;
    --page: #ffffff;
  }
  * { box-sizing: border-box; margin: 0; padding: 0; }
  html, body { width: 972px; height: 1200px; overflow: hidden; background: var(--page); }
  .canvas { position: relative; width: 972px; height: 1200px; }
  .card {
    position: absolute; left: 72px; width: 793px; height: 488px;
    border-radius: 30px; overflow: hidden; background: var(--brand-red);
    box-shadow: 0 2px 6px rgba(0,0,0,0.25);
  }
  .card--front { top: 82px; }
  .card--back { top: 616px; }
  .card__panel { position: absolute; inset: 0; width: 793px; height: 488px; }
  .wordmark {
    position: absolute; left: 56px; top: 172px; width: 400px;
    font-family: "Open Sans", sans-serif; font-weight: 800; font-size: 66px;
    line-height: 1; color: var(--paper); letter-spacing: -1px;
  }
  .tagline {
    position: absolute; left: 56px; top: 248px; width: 372px; text-align: right;
    font-family: "Arimo", sans-serif; font-size: 19px; color: var(--paper);
  }
  .holder { position: absolute; left: 495px; top: 214px; }
  .holder__name {
    font-family: "Open Sans", sans-serif; font-weight: 600; font-size: 19px;
    color: var(--brand-red); letter-spacing: 0.5px; line-height: 1;
  }
  .holder__role {
    margin-top: 6px; font-family: "Open Sans", sans-serif; font-weight: 600;
    font-size: 12px; color: var(--brand-red); letter-spacing: 2.6px; line-height: 1;
  }
  .divider { position: absolute; left: 464px; right: 0; top: 267px; height: 1px; background: var(--brand-red); }
  .contact {
    position: absolute; left: 476px; top: 302px;
    font-family: "Open Sans", sans-serif; font-size: 14.5px; color: var(--ink); line-height: 19px;
  }
  .contact__row { display: flex; align-items: center; gap: 4px; }
  .contact__icon { width: 16px; height: 16px; flex: none; }
  .address {
    position: absolute; left: 482px; top: 359px;
    font-family: "Open Sans", sans-serif; font-size: 14.5px; color: var(--ink); line-height: 19.5px;
  }
  .address__line:nth-child(1) { padding-left: 9px; }
  .address__line:nth-child(2) { padding-left: 6px; }
  .address__line:nth-child(3) { padding-left: 3px; }
  .website {
    position: absolute; left: 485px; top: 231px;
    font-family: "Open Sans", sans-serif; font-weight: 600; font-size: 14px;
    letter-spacing: 3px; color: var(--brand-red);
  }
</style>
</head>
<body>
<main class="canvas">

  <section class="card card--front" aria-label="Business card front">
    <svg class="card__panel" viewBox="0 0 793 488" aria-hidden="true">
      <polygon points="508,0 793,0 793,488 425,488" fill="var(--paper)"/>
    </svg>
    <div class="wordmark">Brightvale</div>
    <div class="tagline">Strategic Innovation</div>

    <div class="holder">
      <div class="holder__name">DANIEL HARCOURT</div>
      <div class="holder__role">FOUNDER &amp; MD</div>
    </div>
    <div class="divider"></div>

    <div class="contact">
      <div class="contact__row">
        <svg class="contact__icon" viewBox="0 0 16 16" aria-hidden="true">
          <circle cx="8" cy="8" r="7" fill="none" stroke="var(--brand-red)" stroke-width="1.5"/>
          <circle cx="8" cy="8" r="2.6" fill="none" stroke="var(--brand-red)" stroke-width="1.5"/>
        </svg>
        <span>daniel@brightvale.com</span>
      </div>
      <div class="contact__row">
        <svg class="contact__icon" viewBox="0 0 16 16" aria-hidden="true">
          <circle cx="8" cy="8" r="7" fill="none" stroke="var(--brand-red)" stroke-width="1.3"/>
          <path d="M5.5 4.2 L7 6 L6.2 7 Q7.2 9 9 9.8 L10 9 L11.8 10.5 L10.8 11.8 Q6.5 11 4.2 5.2 Z" fill="var(--brand-red)"/>
        </svg>
        <span>0715550283</span>
      </div>
    </div>

    <div class="address">
      <div class="address__line">Brightvale (Pty) Ltd</div>
      <div class="address__line">Suite 210, 14 Ashford Ave.</div>
      <div class="address__line">Parkview, JHB, RSA</div>
      <div class="address__line">010 555 0194</div>
    </div>
  </section>

  <section class="card card--back" aria-label="Business card back">
    <svg class="card__panel" viewBox="0 0 793 488" aria-hidden="true">
      <polygon points="508,0 793,0 793,488 425,488" fill="var(--paper)"/>
    </svg>
    <div class="wordmark">Brightvale</div>
    <div class="tagline">Strategic Innovation</div>
    <div class="website">WWW.BRIGHTVALE.COM</div>
  </section>

</main>
</body>
</html>
```